Basic business card

use my newly created logo - and the phrases (Lower Cost of Test & Accelarated New Product Introduction) - and my new email domain / ID - use at conferences / tradeshows

Industry/Entity Type

semiconductor

Contact Information for Business Card

Daniel K Forde, Owner, communicate via Logo - Lower COT - Cost of Test, Accelerated NPI - New Product Introduction, phone +1 555 613 0946, Chandler, Arizona, USA, daniel.forde@qal-vub.com

Font styles to use
Sans Serif

Requirements
Nice to have
• re-use my logo created via Pixel Harbor last August (#7315926)

```html
<!DOCTYPE html>
<html lang="en">
<head>
<meta charset="utf-8">
<title>QAL-VUB Business Card</title>
<link rel="stylesheet" href="https://fonts.googleapis.com/css2?family=Open+Sans:wght@400;600;700&display=swap">
<style>
  :root {
    --page: #e9e7e3;
    --card-dark: #0c0f16;
    --card-mid: #14202f;
    --card-light: #1b2b3f;
    --silver: #9aa3b2;
    --silver-light: #c9cfd8;
    --green: #6cbf3f;
    --blue: #1f80d2;
    --white: #f2f4f7;
    --emblem: #2c4658;
  }
  * { box-sizing: border-box; margin: 0; padding: 0; }
  html, body {
    width: 1200px; height: 780px; overflow: hidden;
    background: var(--page);
    font-family: "Open Sans", Arial, sans-serif;
  }
  .canvas {
    position: relative; width: 1200px; height: 780px;
    display: flex; align-items: center; justify-content: center; gap: 40px;
  }
  .card {
    position: relative; width: 540px; height: 309px; overflow: hidden;
    border-radius: 3px;
    box-shadow: 0 10px 28px rgba(0,0,0,.25);
  }
  .card-front {
    background: linear-gradient(135deg, var(--card-dark) 0%, var(--card-mid) 45%, var(--card-light) 100%);
  }
  .card-back {
    background: radial-gradient(ellipse at 62% 62%, var(--card-light) 0%, var(--card-mid) 45%, var(--card-dark) 100%);
  }

  /* brand name */
  .brand {
    position: absolute; display: flex; align-items: center; gap: 10px;
    color: var(--silver); font-weight: 600; letter-spacing: 1px;
    white-space: nowrap;
  }
  .brand-mark { flex: none; background: var(--silver); opacity: .8; }
  .card-front .brand { left: 22px; top: 16px; font-size: 36px; }
  .card-front .brand-mark { width: 16px; height: 16px; }
  .card-back .brand {
    left: 50%; top: 50%; transform: translate(-50%, -50%);
    font-size: 54px; color: var(--silver-light);
  }
  .card-back .brand-mark { width: 22px; height: 22px; }

  /* large faint emblem area */
  .emblem {
    position: absolute; left: 212px; top: 150px; width: 168px; height: 159px;
    background: var(--emblem); opacity: .5;
  }

  /* person */
  .person { position: absolute; right: 30px; top: 118px; text-align: right; white-space: nowrap; }
  .person-name { font-size: 25px; font-weight: 700; line-height: 1.1; }
  .person-name .first { color: var(--green); }
  .person-name .last { color: var(--blue); }
  .person-title { margin-top: 4px; font-size: 14px; color: var(--white); letter-spacing: .3px; }
  .accent-tab {
    position: absolute; right: 0; top: 172px; width: 14px; height: 34px;
    background: var(--green);
  }

  /* contacts */
  .contact {
    position: absolute; left: 22px; top: 118px;
    font-size: 12px; line-height: 1.55; color: var(--white);
    list-style: none; white-space: nowrap;
  }
  .contact li { display: flex; align-items: center; gap: 6px; }
  .contact .address { padding-left: 16px; }
  .contact svg { width: 10px; height: 10px; flex: none; }
</style>
</head>
<body>
<main class="canvas">

  <section class="card card-front" aria-label="Card front">
    <div class="brand"><span class="brand-mark"></span>QAL-VUB</div>

    <ul class="contact">
      <li class="address">418 Ridgeline Ave. Suite 310</li>
      <li class="address">Chandler, AZ 85226</li>
      <li>
        <svg viewBox="0 0 10 10" aria-hidden="true"><path fill="#6cbf3f" d="M2 1 L4 1 L4.6 3.2 L3.4 4 Q4.2 5.8 6 6.6 L6.8 5.4 L9 6 L9 8 Q5 9 2.4 6.4 Q0.6 4 2 1 Z"/></svg>
        (555) 613-0946
      </li>
      <li>
        <svg viewBox="0 0 10 10" aria-hidden="true"><rect x="0.5" y="2" width="9" height="6.5" rx="1" fill="#6cbf3f"/><path d="M1 2.6 L5 5.6 L9 2.6" stroke="#0c0f16" stroke-width="1" fill="none"/></svg>
        hello@qal-vub.com
      </li>
      <li>
        <svg viewBox="0 0 10 10" aria-hidden="true"><circle cx="5" cy="5" r="4.5" fill="#6cbf3f"/><path d="M0.8 5 H9.2 M5 0.6 Q2.6 5 5 9.4 M5 0.6 Q7.4 5 5 9.4" stroke="#0c0f16" stroke-width=".8" fill="none"/></svg>
        www.qal-vub.com
      </li>
    </ul>

    <div class="emblem" role="img" aria-label="Large faint brand emblem area"></div>

    <div class="person">
      <p class="person-name"><span class="first">Lena</span> <span class="last">Varga</span></p>
      <p class="person-title">Managing Director</p>
    </div>
    <div class="accent-tab"></div>
  </section>

  <section class="card card-back" aria-label="Card back">
    <div class="brand"><span class="brand-mark"></span>QAL-VUB</div>
  </section>

</main>
</body>
</html>
```